Buch-/eBook-Cover zum Thema Magersucht
Zielgruppe
Ich bin Autorin und suche ein passendes Buchcover. Die Zielgruppe für dieses Buch sind Eltern von magersüchtigen Kindern sowie interessierte medizinische und therapeutische Fachkräfte.
Aufgabenstellung
Bei meinem Buch handelt es sich um einen Ratgeber zur Behandlung von Magersucht bei Kindern und Jugendlichen.
Folgendes muss auf die Vorderseite des Buches:
Titel: Teller trägt Trost
Untertitel: Elterngestützte Begleitung im Alltag
Helga Brunsmeier
Ich wünsche mir ein einfühlsames Cover, das die Schwere der Krankheit spiegelt, aber auch die Hoffnung auf Heilung. Bitte keine plumpen Bilder von Waage, Massband oder dünnen Körpern.
Der Klappentext im Word-Dokument ist für die Rückseite des Buchcovers.

```html
<!DOCTYPE html>
<html lang="de">
<head>
<meta charset="utf-8">
<title>Teller trägt Trost – Buchumschlag</title>
<link rel="stylesheet" href="https://fonts.googleapis.com/css2?family=Jost:wght@400;500;600&family=Karla:wght@400&family=Work+Sans:wght@400&display=swap">
<style>
  :root {
    --page: #ffffff;
    --back-bg: #fbfbfd;
    --spine-bg: #1fa58a;
    --front-bg: #9ca5b8;
    --ink: #0f2a2a;
    --ink-body: #1c2626;
    --art-warm: #f28c1e;
    --art-cool: #1bb092;
    --art-red: #ec2f45;
  }
  * { margin: 0; padding: 0; box-sizing: border-box; }
  html, body {
    width: 1200px; height: 1178px; overflow: hidden;
    background: var(--page);
  }
  .wrap {
    position: absolute; left: 62px; top: 228px;
    width: 1079px; height: 789px;
    display: flex;
  }
  .back-cover {
    width: 519px; height: 100%;
    background: var(--back-bg);
    position: relative;
  }
  .spine {
    width: 35px; height: 100%;
    background: var(--spine-bg);
    position: relative;
    overflow: hidden;
  }
  .front-cover {
    width: 525px; height: 100%;
    background: var(--front-bg);
    position: relative;
  }
  .title {
    font-family: "Jost", sans-serif;
    color: var(--ink);
    text-align: center;
    line-height: 1;
  }
  .title .big { display: block; font-weight: 600; letter-spacing: 0.08em; }
  .title .small { display: block; font-weight: 400; }

  .back-cover .title { position: absolute; left: 0; right: 0; top: 44px; }
  .back-cover .title .big { font-size: 46px; }
  .back-cover .title .small { font-size: 36px; margin: 2px 0 4px; }

  .blurb {
    position: absolute; left: 38px; top: 216px; width: 460px;
    font-family: "Karla", sans-serif; font-size: 14.2px; line-height: 21.7px;
    color: var(--ink-body);
    hyphens: auto;
  }
  .blurb p + p { margin-top: 21.7px; }

  .author {
    font-family: "Karla", sans-serif; color: var(--ink);
    position: absolute; left: 0; right: 0; text-align: center;
    font-size: 23px; letter-spacing: 0.01em;
  }
  .back-cover .author { top: 713px; }
  .front-cover .author { top: 72px; }

  .spine-text {
    position: absolute; top: 80px; left: 50%;
    transform: translateX(-50%);
    writing-mode: vertical-rl;
    white-space: nowrap;
    font-family: "Jost", sans-serif; font-size: 16px; line-height: 1;
    color: var(--ink);
    letter-spacing: 0.04em;
  }
  .spine-text b { font-weight: 600; }

  .front-cover .title { position: absolute; left: 0; right: 0; top: 160px; padding-left: 20px; }
  .front-cover .title .big { font-size: 66px; }
  .front-cover .title .small { font-size: 50px; margin: 2px 0 4px; }

  .cover-art {
    position: absolute; left: 40px; top: 358px; width: 464px; height: 220px;
    border-radius: 6px;
    background: linear-gradient(100deg, var(--art-red) 0%, var(--art-cool) 30%, var(--art-warm) 60%, var(--art-cool) 85%, var(--art-red) 100%);
    opacity: 0.85;
  }
  .subtitle {
    position: absolute; left: 0; right: 0; top: 604px;
    padding-left: 20px;
    text-align: center;
    font-family: "Work Sans", sans-serif; font-size: 23px; color: var(--ink);
    letter-spacing: 0.01em;
  }
</style>
</head>
<body>
  <div class="wrap">
    <section class="back-cover">
      <h2 class="title"><span class="big">TELLER</span><span class="small">trägt</span><span class="big">TROST</span></h2>
      <div class="blurb">
        <p>Anorexia Nervosa - Magersucht - ist eine genetisch veranlagte, psychobiologische Krankheit mit einer Sterberate von 10-15%.<br>Je früher die Krankheit diagnostiziert wird, je jünger die Patient:innen bei der Diagnose sind, je rascher mit der Wiederernährung begonnen wird und je schneller ein individuelles gesundes Gewicht erreicht wird, desto grösser ist die langfristige Heilungschance.</p>
        <p>Bei Kindern und Jugendlichen ist gemäß der modernen Anorexie-Forschung die Familie nicht das Problem, sondern in der Regel die größte Ressource für die Heilung. Bei der familienbasierten Pflege zuhause steht die rasche Wiederherstellung des gesunden Gewichts im Vordergrund. Die Eltern übernehmen die volle Verantwortung für die Wiederernährung ihres kranken Kindes, bis sich dessen Verhalten normalisiert hat.</p>
        <p>Dieser Ratgeber liefert ein tiefes Verständnis für die Krankheit auf Basis moderner wissenschaftlicher Erkenntnisse. Er unterstützt Eltern in der Pflege ihrer Kinder zuhause anhand zahlreicher Tipps und erprobter Praxisbeispiele. Von Kochrezepten über den Umgang mit Angst, Aggression und Essensverweigerung bis hin zum Thema Selbstfürsorge ist er eine unentbehrliche Quelle für alle Eltern, die ihre Kinder in die Genesung begleiten möchten. Anorexie ist heilbar.</p>
      </div>
      <p class="author">Helga Brunsmeier</p>
    </section>
    <div class="spine">
      <p class="spine-text"><b>TELLER</b> trägt <b>TROST</b> – Elterngestützte Begleitung im Alltag</p>
    </div>
    <section class="front-cover">
      <p class="author">Helga Brunsmeier</p>
      <h1 class="title"><span class="big">TELLER</span><span class="small">trägt</span><span class="big">TROST</span></h1>
      <div class="cover-art" role="img" aria-label="Illustration: bunte Holzbauklötze balancieren auf einer Wippe"></div>
      <p class="subtitle">Elterngestützte Begleitung im Alltag</p>
    </section>
  </div>
</body>
</html>
```